Card Design for my dog training business Brightpaw Obedience

Need a business card design for my dog training business with my new logo. Want the card to come off professional yet fun. Want it to be very eye catchy as well. I normally have these at vet clinics, pet stores, and groomers. so need it to look better than my competitors.
Target Market(s)
dog owners
Industry/Entity Type
Dog Training
Contact Information for Business Card
needs logo, my name and info
Font styles to use
Serif
Colors
0255a3
ffffff
ec1f27
000000
333333
fbfbfb
Requirements
Must have
- Brightpaw Obedience
- Felix Orland
- 415 903 2276
- info@brightpawobedience.example
- www.brightpawobedience.example

```html
<!DOCTYPE html>
<html lang="en">
<head>
<meta charset="utf-8">
<title>Brightpaw Obedience – Business Card</title>
<link rel="stylesheet" href="https://fonts.googleapis.com/css2?family=Cinzel:wght@500&family=Lato:wght@400&display=swap">
<style>
  :root {
    --backdrop: #161616;
    --card: #1f1f1f;
    --card-edge: #2a2a2a;
    --silver: #d9d9d9;
    --silver-soft: #a8a8a8;
    --deboss: #121212;
    --deboss-light: #2e2e2e;
  }
  * { margin: 0; padding: 0; box-sizing: border-box; }
  html, body {
    width: 1200px; height: 900px; overflow: hidden;
    background: var(--backdrop);
  }
  .canvas {
    position: relative; width: 1200px; height: 900px;
    display: flex; flex-direction: column; align-items: center;
    justify-content: center; gap: 28px;
  }
  .card {
    position: relative; width: 640px; height: 366px;
    background: linear-gradient(135deg, var(--card) 0%, #232323 60%, #1b1b1b 100%);
    border: 1px solid var(--card-edge);
    box-shadow: 0 18px 40px rgba(0,0,0,0.55);
  }
  .card-front { display: flex; align-items: center; justify-content: center; }
  .brand {
    display: flex; align-items: center; gap: 14px;
    font-family: "Cinzel", serif; font-weight: 500;
    font-size: 30px; letter-spacing: 3px; color: var(--silver);
  }
  .brand-dot { width: 14px; height: 14px; border-radius: 50%; background: var(--silver); }
  .card-back { display: flex; align-items: center; }
  .identity { width: 300px; text-align: right; padding-right: 24px; }
  .holder-name {
    font-family: "Cinzel", serif; font-weight: 500; font-size: 19px;
    letter-spacing: 1.5px; color: var(--deboss);
    text-shadow: 0 1px 0 var(--deboss-light);
  }
  .holder-role {
    margin-top: 4px; font-family: "Lato", sans-serif; font-size: 16px;
    color: var(--deboss); text-shadow: 0 1px 0 var(--deboss-light);
  }
  .divider { width: 1px; height: 70px; background: var(--silver-soft); }
  .contacts { list-style: none; padding-left: 24px; }
  .contact {
    display: flex; align-items: center; gap: 12px;
    font-family: "Lato", sans-serif; font-size: 16px; line-height: 27px;
    color: var(--silver);
  }
  .contact svg { width: 12px; height: 12px; flex: none; }
</style>
</head>
<body>
<main class="canvas">
  <section class="card card-front" aria-label="Card front">
    <div class="brand"><span class="brand-dot"></span><span>Brightpaw Obedience</span></div>
  </section>

  <section class="card card-back" aria-label="Card back">
    <div class="identity">
      <p class="holder-name">FELIX ORLAND</p>
      <p class="holder-role">Managing Director</p>
    </div>
    <div class="divider"></div>
    <ul class="contacts">
      <li class="contact">
        <svg viewBox="0 0 12 12" aria-hidden="true"><path d="M3 1 L5 3.5 L4 4.8 Q5 7 7.2 8 L8.5 7 L11 9 L10 11 Q4 11 1 2 Z" fill="var(--silver-soft)"/></svg>
        <span>415 903 2276</span>
      </li>
      <li class="contact">
        <svg viewBox="0 0 12 12" aria-hidden="true"><rect x="1" y="2.5" width="10" height="7" fill="none" stroke="var(--silver-soft)" stroke-width="1"/><path d="M1 2.5 L6 6.5 L11 2.5" fill="none" stroke="var(--silver-soft)" stroke-width="1"/></svg>
        <span>info@brightpawobedience.example</span>
      </li>
      <li class="contact">
        <svg viewBox="0 0 12 12" aria-hidden="true"><circle cx="6" cy="6" r="5" fill="none" stroke="var(--silver-soft)" stroke-width="1"/><ellipse cx="6" cy="6" rx="2.2" ry="5" fill="none" stroke="var(--silver-soft)" stroke-width="0.8"/><path d="M1 6 H11" stroke="var(--silver-soft)" stroke-width="0.8"/></svg>
        <span>www.brightpawobedience.example</span>
      </li>
    </ul>
  </section>
</main>
</body>
</html>
```